Business cards, poster and standing banners for Brindlefest.org needed under 48h!

Hi Genius designers,
I have a seemingly very simple project, I am organizing a open source hardware hackathon (www.brindlefest.org) and need 6 deliverables:
1) a better looking png logo with transparent background (one light grey, one dark grey color. Only the middle Anarchy A have to remain red) (deadline March 18)
2) a better looking square picture (for social media identity) (deadline March 18)
3) business cards (deadline March 18) (name, email, mobile, twitter, www.brindlefest.org)
4) A3 poster (deadline March 18), should include:
- Tagline: Non-profit Open Source Hardware Hardware
- Date: March 28-30
- Venue: Gearloft Bayside Annex, 712 Pelling Rd, San Carlos
- Join the Hardware renaissance!
- www.brindlefest.org
- QR code (attached)
5) standard standing banners (deadline March 20)
I attached existing logo just need it to be better, and a background picture to use for all these marketing materials. Just need someone to make all these very professional.
Attached:
- existing logo
- existing square image for social media identity
- bakcground
- QR code to include in A3 poster
Updates
Please use existing logo, i am not looking for a new logo, just need a professional version of the existing logo (anarchy A in red)
20-35 entrepreneurs, new generation of hardware engineers, makers
Marketing

```html
<!DOCTYPE html>
<html lang="en">
<head>
<meta charset="utf-8">
<title>Brindlefest Business Card</title>
<link href="https://fonts.googleapis.com/css2?family=Source+Sans+3:wght@400;600;700&display=swap" rel="stylesheet">
<style>
  :root {
    --backdrop: #2b2c2d;
    --card-light: #ffffff;
    --card-edge: #e6e7e8;
    --ink-strong: #555658;
    --ink-soft: #6a6b6d;
    --divider: #b9babb;
    --mark-faint: #e3e4e5;
  }
  html, body {
    margin: 0;
    padding: 0;
    width: 1200px;
    height: 946px;
    overflow: hidden;
    background: var(--backdrop);
    font-family: "Source Sans 3", "Myriad Pro", Arial, sans-serif;
  }
  .stage {
    position: relative;
    width: 1200px;
    height: 946px;
    display: flex;
    align-items: center;
    justify-content: center;
  }
  .business-card {
    position: relative;
    width: 880px;
    height: 503px;
    border-radius: 42px;
    background: radial-gradient(ellipse at 50% 45%, var(--card-light) 0%, #f4f4f5 55%, var(--card-edge) 100%);
    box-shadow: 0 18px 40px rgba(0, 0, 0, 0.55);
    overflow: hidden;
  }
  .card-divider {
    position: absolute;
    left: 500px;
    top: 44px;
    width: 3px;
    height: 420px;
    background: linear-gradient(to bottom, rgba(185,186,187,0) 0%, var(--divider) 35%, var(--divider) 75%, rgba(185,186,187,0) 100%);
  }
  .brand-name {
    position: absolute;
    left: 62px;
    top: 118px;
    margin: 0;
    font-size: 60px;
    font-weight: 700;
    letter-spacing: -1px;
    color: var(--ink-strong);
    line-height: 1;
  }
  .contact-list {
    position: absolute;
    left: 66px;
    bottom: 54px;
    margin: 0;
    padding: 0;
    list-style: none;
  }
  .contact-item {
    display: flex;
    align-items: center;
    gap: 14px;
    height: 38px;
    font-size: 22px;
    color: var(--ink-soft);
  }
  .contact-icon {
    width: 24px;
    height: 24px;
    flex: none;
  }
  .holder {
    position: absolute;
    left: 548px;
    top: 78px;
  }
  .holder-name {
    margin: 0;
    font-size: 29px;
    font-weight: 600;
    color: var(--ink-strong);
    line-height: 1.2;
  }
  .holder-role {
    margin: 2px 0 0;
    font-size: 24px;
    font-weight: 400;
    color: var(--ink-soft);
  }
  .faint-mark {
    position: absolute;
    right: 40px;
    bottom: 60px;
    width: 190px;
    height: 190px;
    border-radius: 50%;
    background: var(--mark-faint);
    opacity: 0.8;
  }
</style>
</head>
<body>
<main class="stage">
  <article class="business-card">
    <h1 class="brand-name">BRINDLEFEST</h1>

    <ul class="contact-list">
      <li class="contact-item">
        <svg class="contact-icon" viewBox="0 0 24 24" aria-hidden="true">
          <rect x="6" y="1.5" width="12" height="21" rx="2" fill="none" stroke="#6a6b6d" stroke-width="1.8"/>
          <line x1="6" y1="18" x2="18" y2="18" stroke="#6a6b6d" stroke-width="1.5"/>
          <circle cx="12" cy="20.2" r="0.9" fill="#6a6b6d"/>
        </svg>
        <span>555.014.2100</span>
      </li>
      <li class="contact-item">
        <svg class="contact-icon" viewBox="0 0 24 24" aria-hidden="true">
          <rect x="2" y="5" width="20" height="14" rx="1.5" fill="none" stroke="#6a6b6d" stroke-width="1.8"/>
          <polyline points="2.5,6 12,13 21.5,6" fill="none" stroke="#6a6b6d" stroke-width="1.6"/>
        </svg>
        <span>info@brindlefest.org</span>
      </li>
      <li class="contact-item">
        <svg class="contact-icon" viewBox="0 0 24 24" aria-hidden="true">
          <circle cx="12" cy="12" r="10" fill="none" stroke="#6a6b6d" stroke-width="1.7"/>
          <ellipse cx="12" cy="12" rx="4.5" ry="10" fill="none" stroke="#6a6b6d" stroke-width="1.4"/>
          <line x1="2" y1="12" x2="22" y2="12" stroke="#6a6b6d" stroke-width="1.4"/>
          <line x1="4" y1="7" x2="20" y2="7" stroke="#6a6b6d" stroke-width="1.2"/>
          <line x1="4" y1="17" x2="20" y2="17" stroke="#6a6b6d" stroke-width="1.2"/>
        </svg>
        <span>brindlefest.org</span>
      </li>
      <li class="contact-item">
        <svg class="contact-icon" viewBox="0 0 24 24" aria-hidden="true">
          <circle cx="12" cy="12" r="8" fill="#6a6b6d"/>
        </svg>
        <span>@brindlefest</span>
      </li>
    </ul>

    <div class="card-divider"></div>

    <div class="holder">
      <p class="holder-name">Person’s Name</p>
      <p class="holder-role">Designation</p>
    </div>

    <div class="faint-mark" aria-hidden="true"></div>
  </article>
</main>
</body>
</html>
```